Classy, Elegant, Simple Business Card Design

Looking to have a classy, simple, and elegant design. Want a top notch designed business card. I really like the look of the new torvane credit card. I also like the design I attached. I am trying to reach 21-29 year old females for booking us for there wedding or event. We offer Disc Jockey Service, Photo Booth Rentals, and Uplighting .

Target Market(s)

21-28 year old females

Contact Information for Business Card

Has to have logo, website, email, and phone number

Font styles to use
Other font styles liked:
• open to font choice, modern, clean
Designer to choose
33a6d7
0791cd
0555a3
ffffff

Requirements
Must have
• Has to have logo, website, email, and phone number
Nice to have
• I really like the design of the new torvane credit card. I also included my logo and some designs I like
Should not have
• clutter or too much info

```html
<!DOCTYPE html>
<html lang="en">
<head>
<meta charset="utf-8">
<title>Lumenhall Business Card</title>
<link href="https://fonts.googleapis.com/css2?family=Mulish:wght@700&family=Roboto:wght@400;500&display=swap" rel="stylesheet">
<style>
  :root {
    --page-bg: #d8d3cb;
    --card-bg: #eef1f2;
    --card-edge: #ffffff;
    --ink: #2b2f33;
    --brand-deep: #0555a3;
    --brand-mid: #0791cd;
    --brand-light: #33a6d7;
    --icon: #1f5f8f;
  }
  html, body {
    margin: 0;
    padding: 0;
    width: 1200px;
    height: 1054px;
    overflow: hidden;
    background: var(--page-bg);
  }
  .card {
    position: absolute;
    left: 120px;
    top: 238px;
    width: 960px;
    height: 578px;
    background: linear-gradient(135deg, #f3f5f6 0%, var(--card-bg) 55%, #e6eaec 100%);
    border: 1px solid var(--card-edge);
    box-shadow: 0 10px 30px rgba(0,0,0,0.12);
    font-family: "Roboto", Arial, sans-serif;
    color: var(--ink);
  }
  .holder {
    position: absolute;
    right: 58px;
    top: 70px;
    text-align: right;
  }
  .holder-name {
    margin: 0;
    font-family: "Mulish", "Century Gothic", sans-serif;
    font-weight: 700;
    font-size: 37px;
    line-height: 1.1;
    color: var(--brand-deep);
  }
  .holder-title {
    margin: 6px 0 0;
    font-size: 22px;
    color: var(--ink);
  }
  .brand {
    position: absolute;
    left: 66px;
    top: 440px;
    display: flex;
    align-items: center;
    gap: 14px;
  }
  .brand-dot {
    width: 26px;
    height: 26px;
    border-radius: 50%;
    background: var(--brand-mid);
  }
  .brand-name {
    font-family: "Roboto", Arial, sans-serif;
    font-weight: 500;
    font-size: 38px;
    letter-spacing: 1px;
    color: var(--brand-deep);
  }
  .contact {
    position: absolute;
    right: 50px;
    top: 420px;
    margin: 0;
    padding: 0;
    list-style: none;
  }
  .contact-item {
    display: flex;
    justify-content: flex-end;
    align-items: center;
    gap: 18px;
    height: 38px;
    font-size: 23px;
    color: var(--ink);
  }
  .contact-icon {
    width: 22px;
    height: 22px;
    fill: var(--icon);
    flex: none;
  }
</style>
</head>
<body>
  <div class="card">
    <div class="holder">
      <h1 class="holder-name">Claire Dalton</h1>
      <p class="holder-title">Founder &amp; CEO</p>
    </div>

    <div class="brand">
      <span class="brand-dot"></span>
      <span class="brand-name">LUMENHALL</span>
    </div>

    <ul class="contact">
      <li class="contact-item">
        <span>555 0142 0187</span>
        <svg class="contact-icon" viewBox="0 0 24 24" aria-hidden="true">
          <path d="M3 9c0-3 4-5 9-5s9 2 9 5v1.5h-4V8.5c-1.5-.7-3.2-1-5-1s-3.5.3-5 1v2H3z"/>
          <path d="M6 12h12l2 8H4z M9 14h6v4H9z" fill-rule="evenodd"/>
        </svg>
      </li>
      <li class="contact-item">
        <span>claire@lumenhall.com</span>
        <svg class="contact-icon" viewBox="0 0 24 24" aria-hidden="true">
          <path d="M2 5h20v14H2z M4 7.5v9.5h16V7.5l-8 6z M5 7l7 5.2L19 7z" fill-rule="evenodd"/>
        </svg>
      </li>
      <li class="contact-item">
        <span>www.lumenhall.com</span>
        <svg class="contact-icon" viewBox="0 0 24 24" aria-hidden="true">
          <circle cx="12" cy="12" r="10"/>
          <path d="M2 12h20 M12 2c3 3 3 17 0 20 M12 2c-3 3-3 17 0 20 M4 7h16 M4 17h16" stroke="#eef1f2" stroke-width="1.3" fill="none"/>
        </svg>
      </li>
    </ul>
  </div>
</body>
</html>
```